Brightfield Ventures Inc. Letterhead

Creation of attractive and eye catching letterhead for a business start-up for the construction industry. Letterhead must relate to construction, but avoid standard hammer and tools in the design.

I forgot to add some details, sorry about that. Some pertinent info: Ph: 916-555-0187 brightfieldventures.example 448 Willowmere Ave, Ste 210 Folsom, CA 95999 info@brightfieldventures.example not sure if slogan should be in there" “Connecting construction professionals to create a purpose driven industry.” must be able to be used in word. Thanks!

```html
<!DOCTYPE html>
<html lang="en">
<head>
<meta charset="utf-8">
<title>Brightfield Ventures Inc. Letterhead</title>
<link href="https://fonts.googleapis.com/css2?family=Arimo:wght@700&family=Source+Sans+3:wght@400;600&display=swap" rel="stylesheet">
<style>
  :root {
    --canvas-bg: #e3e3e3;
    --paper: #fbfbfb;
    --navy: #1f2a6b;
    --brand-red: #b8070c;
    --ink: #2a2a2a;
    --footer-ink: #ffffff;
    --signature-tone: #d6d6d6;
  }
  * { margin: 0; padding: 0; box-sizing: border-box; }
  html, body {
    width: 1200px; height: 945px; overflow: hidden;
    background: var(--canvas-bg);
  }
  .letterhead {
    position: absolute; left: 280px; top: 20px;
    width: 640px; height: 905px;
    background: var(--paper);
    box-shadow: 0 2px 10px rgba(0,0,0,.12);
    font-family: "Source Sans 3", sans-serif;
    color: var(--ink);
  }
  .brand {
    position: absolute; left: 48px; top: 46px;
    display: flex; align-items: center; gap: 8px;
  }
  .brand-square { width: 14px; height: 14px; background: var(--brand-red); }
  .brand-name {
    font-weight: 600; font-size: 19px; color: var(--navy);
    letter-spacing: .02em;
  }
  .letter-body {
    position: absolute; left: 64px; top: 168px; width: 512px;
    font-size: 12.6px; line-height: 1.22;
  }
  .salutation {
    font-family: "Arimo", sans-serif; font-weight: 700;
    font-size: 14px; margin-bottom: 16px;
  }
  .letter-body p.para { margin-bottom: 16px; }
  .signature {
    position: absolute; left: 64px; top: 700px;
    width: 130px; height: 42px; border-radius: 4px;
    background: linear-gradient(90deg, var(--signature-tone), #ececec);
  }
  .footer-band {
    position: absolute; left: 0; bottom: 34px; width: 640px; height: 58px;
  }
  .footer-text {
    position: absolute; left: 300px; bottom: 44px;
    color: var(--footer-ink); font-size: 10.5px; line-height: 1.45;
  }
  .footer-text b { font-weight: 600; }
</style>
</head>
<body>
  <main class="letterhead">
    <header class="brand">
      <span class="brand-square"></span>
      <span class="brand-name">Brightfield Ventures Inc.</span>
    </header>

    <section class="letter-body">
      <p class="salutation">Dear Mr. Carter,</p>
      <p class="para">Lorem Ipsum is simply dummy text of the printing and typesetting industry. Lorem Ipsum has been the industry's standard dummy text ever since the 1500s, when an unknown printer took a galley of type and scrambled it to make a type specimen book. It has survived not only five centuries, but also the leap into electronic typesetting, remaining essentially unchanged.</p>
      <p class="para">The standard chunk of Lorem Ipsum used since the 1500s is reproduced below for those interested. Sections 1.10.32 and 1.10.33 from "de Finibus Bonorum et Malorum" by Varennius are also reproduced in their exact original form, accompanied by English versions from the 1914 translation by H.Lindqvist</p>
      <p class="para">Lorem Ipsum is simply dummy text of the printing and typesetting industry. Lorem Ipsum has been the industry's standard dummy text ever since the 1500s, when an unknown printer took a galley of type and scrambled it to make a type specimen book. It has survived not only five centuries, but also the leap into electronic typesetting, remaining essentially unchanged. It was popularised in the</p>
      <p class="para">The standard chunk of Lorem Ipsum used since the 1500s is reproduced below for those interested. Sections 1.10.32 and 1.10.33 from "de Finibus Bonorum et Malorum" by Varennius are also reproduced in their exact original form, accompanied by English versions from the 1914 translation by H.Lindqvist</p>
      <p class="para">The standard chunk of Lorem Ipsum used since the 1500s is reproduced below for those interested. Sections 1.10.32 and 1.10.33 from "de Finibus Bonorum et Malorum" by Varennius are also reproduced in their exact original form.</p>
    </section>

    <div class="signature" role="img" aria-label="Handwritten signature"></div>

    <svg class="footer-band" viewBox="0 0 640 58" aria-hidden="true">
      <polygon points="270,0 640,0 640,58 230,58" fill="var(--brand-red)"/>
      <polyline points="190,58 240,10 270,0" fill="none" stroke="var(--brand-red)" stroke-width="2"/>
    </svg>
    <footer class="footer-text">
      448 Willowmere Ave, Ste 210, Folsom, CA 95999<br>
      <b>P :</b> 916-555-0187 &nbsp;<b>E :</b> info@brightfieldventures.example &nbsp;|&nbsp; brightfieldventures.example
    </footer>
  </main>
</body>
</html>
```